KRWB new business card design

We need a business card design for our established business which is Australia wide however based in Melbourne. We are a young team of Financial Planners who specialize in Insurance and Basic super advice for people like us.

We are people who help our clients get things done in a timely and cost effective manner whilst having a good time and a laugh along the way.

We would like this to have a consistent feel with our new e-brochure which i have attached from a color and font perspective.

Industry/Entity Type

Business

Requirements
Must have
• We do not need specific address details rather just the states we are in:

VIC/NSW/QLD/TAS
Nice to have
• Curved edge to mate the brochure

```html
<!DOCTYPE html>
<html lang="en">
<head>
<meta charset="utf-8">
<title>KRWB Business Card</title>
<link href="https://fonts.googleapis.com/css2?family=Exo+2:wght@600;700&family=Roboto:ital,wght@0,400;0,500;1,400&display=swap" rel="stylesheet">
<style>
  :root {
    --page: #e6e4e0;
    --card-black: #0b0b0b;
    --mesh: #2a2a2c;
    --green: #4caf3f;
    --white: #f4f4f4;
    --grey-text: #cfcfcf;
    --rule: #444;
    --silver-a: #6d6d6d;
    --silver-b: #e9e9e9;
  }
  * { box-sizing: border-box; margin: 0; padding: 0; }
  html, body { width: 1200px; height: 880px; overflow: hidden; background: var(--page); }
  .canvas { position: relative; width: 1200px; height: 880px; }

  .card {
    position: absolute;
    width: 540px; height: 310px;
    background: var(--card-black);
    border-radius: 4px;
    overflow: hidden;
    box-shadow: 0 6px 18px rgba(0,0,0,.18);
  }
  .card--back { left: 600px; top: 90px; }
  .card--front { left: 60px; top: 480px; }

  .card__shapes { position: absolute; inset: 0; }

  /* brand stand-in */
  .brand { position: absolute; display: flex; align-items: center; gap: 12px; }
  .brand__mark { width: 44px; height: 44px; background: var(--green); flex: none; }
  .brand__name {
    font-family: "Exo 2", sans-serif; font-weight: 700;
    color: var(--white); letter-spacing: 1px; line-height: 1;
  }
  .card--back .brand {
    right: 22px; top: 96px; width: 104px;
    flex-direction: column; gap: 10px;
  }
  .card--back .brand__mark { width: 34px; height: 34px; }
  .card--back .brand__name { font-size: 30px; }
  .card--front .brand { left: 50%; top: 82px; transform: translateX(-50%); }
  .card--front .brand__name { font-size: 60px; }

  /* back card details */
  .contact { position: absolute; left: 40px; top: 30px; width: 300px; }
  .contact__name {
    font-family: "Exo 2", sans-serif; font-weight: 700; font-size: 19px; color: var(--white);
  }
  .contact__name .post { font-family: "Roboto", sans-serif; font-style: italic; font-weight: 400; font-size: 13px; color: var(--green); }
  .contact__role { font-family: "Roboto", sans-serif; font-size: 14px; color: var(--white); margin-top: 3px; }
  .contact__entity { font-family: "Roboto", sans-serif; font-style: italic; font-size: 9px; line-height: 1.3; color: var(--green); margin-top: 8px; }
  .contact__list { list-style: none; margin-top: 14px; font-family: "Roboto", sans-serif; font-size: 13px; color: var(--grey-text); }
  .contact__list li { display: flex; align-items: center; gap: 10px; height: 20px; }
  .contact__list svg { width: 12px; height: 12px; flex: none; }
  .contact__rule { height: 1px; background: var(--rule); margin: 8px 0; width: 220px; }

  /* front card */
  .silver-line {
    position: absolute; left: 0; right: 0; top: 232px; height: 6px;
    background: linear-gradient(90deg, var(--silver-a), var(--silver-b) 45%, var(--silver-a) 80%, #2a2a2a);
  }
  .states {
    position: absolute; left: 0; right: 0; bottom: 0; height: 72px;
    display: flex; align-items: center; justify-content: center; gap: 10px;
    padding: 0 20px;
    font-family: "Exo 2", sans-serif; font-weight: 700; font-size: 14px; letter-spacing: 1px;
    color: var(--white); list-style: none; white-space: nowrap;
  }
  .states li { display: flex; align-items: center; gap: 10px; }
  .states li + li::before {
    content: ""; width: 6px; height: 6px; border-radius: 50%; background: var(--green);
  }
</style>
</head>
<body>
<main class="canvas">

  <section class="card card--back" aria-label="Business card, contact side">
    <svg class="card__shapes" viewBox="0 0 540 310" width="540" height="310">
      <path d="M418 0 H540 V310 H200 C330 310 392 262 398 170 L418 0 Z" fill="var(--mesh)" role="img" aria-label="Dark hexagon mesh texture panel"/>
      <path d="M418 0 L398 170 C392 262 330 310 200 310" fill="none" stroke="var(--green)" stroke-width="7"/>
    </svg>

    <div class="contact">
      <p class="contact__name">Daniel Hartley <span class="post">BAppSc</span></p>
      <p class="contact__role">Practice Growth Manager</p>
      <p class="contact__entity">KRWB Advice Pty Ltd<br>Authorised Rep. of Summitline Planning Ltd<br>Australian Financial Services Licensee</p>
      <ul class="contact__list">
        <li><svg viewBox="0 0 12 12"><rect width="12" height="12" rx="2" fill="var(--green)"/><path d="M3 3.5 C3 7 5 9 8.5 9 L9 7.5 L7.5 6.8 L7 7.5 C5.8 7 5 6.2 4.5 5 L5.2 4.5 L4.5 3 Z" fill="var(--card-black)"/></svg>1300 555 014</li>
        <li><svg viewBox="0 0 12 12"><rect x="2.5" width="7" height="12" rx="1.5" fill="var(--green)"/><rect x="4" y="2" width="4" height="6" fill="var(--card-black)"/></svg>0400 555 218</li>
      </ul>
      <div class="contact__rule"></div>
      <ul class="contact__list">
        <li><svg viewBox="0 0 12 12"><rect y="2" width="12" height="8" rx="1" fill="var(--green)"/><path d="M1 3 L6 7 L11 3" fill="none" stroke="var(--card-black)" stroke-width="1"/></svg>hello@krwb.com.au</li>
        <li><svg viewBox="0 0 12 12"><circle cx="6" cy="6" r="5.5" fill="var(--green)"/><path d="M1 6 H11 M6 0.5 C3 3.5 3 8.5 6 11.5 M6 0.5 C9 3.5 9 8.5 6 11.5" fill="none" stroke="var(--card-black)" stroke-width=".8"/></svg>www.krwb.com.au</li>
      </ul>
      <div class="contact__rule"></div>
    </div>

    <div class="brand">
      <span class="brand__mark"></span>
      <span class="brand__name">KRWB</span>
    </div>
  </section>

  <section class="card card--front" aria-label="Business card, brand side">
    <svg class="card__shapes" viewBox="0 0 540 310" width="540" height="310">
      <rect width="540" height="232" fill="var(--mesh)" role="img" aria-label="Dark hexagon mesh texture panel"/>
    </svg>
    <div class="brand">
      <span class="brand__mark"></span>
      <span class="brand__name">KRWB</span>
    </div>
    <div class="silver-line"></div>
    <ul class="states">
      <li>VICTORIA</li>
      <li>NEW SOUTH WALES</li>
      <li>QUEENSLAND</li>
      <li>TASMANIA</li>
    </ul>
  </section>

</main>
</body>
</html>
```